Tovimar Community Development Planning New web site

Design a new web site. I have a budget of $1,500.00.
Attached on PowerPoint is a complete site plan. Home page and linked pages.
10 - 12 pages. All copy and photos will be supplied. (300dpi)
I have shown them the concept which they like.
No data bases required. Home page with animations dissolving.
They former web site has been taken down. They have been in business 30 years in New Jersey
Colors teal blues and greens
There will be a new logo)being designed)
The text in home page copy will give you a detailed story what they are all about.

files have been approved for Tovimar, Inc.   Brenton is the designer

```html
<!DOCTYPE html>
<html lang="en">
<head>
<meta charset="utf-8">
<title>Tovimar Inc – Community Development Planning</title>
<link rel="stylesheet" href="https://fonts.googleapis.com/css2?family=Catamaran:wght@400;500;600&family=Hind:wght@400;500&family=Raleway:wght@400;500&display=swap">
<style>
  :root {
    --green: #4d9b15;
    --yellow: #f2c300;
    --ink: #1e1e1e;
    --body: #3a3a3a;
    --muted: #8a8a8a;
    --rule: #d6d6d6;
    --white: #ffffff;
    --band: rgba(55, 55, 55, 0.62);
    --photo-block: #7fa7b8;
  }
  * { box-sizing: border-box; margin: 0; padding: 0; }
  html, body { width: 928px; height: 1200px; overflow: hidden; background: var(--white); }
  body { position: relative; font-family: "Hind", sans-serif; color: var(--body); }

  .site-header { position: absolute; left: 0; top: 0; width: 928px; height: 47px; background: var(--green); }
  .brand { position: absolute; left: 33px; top: 6px; font-family: "Catamaran", sans-serif; font-weight: 600; font-size: 27px; color: var(--white); letter-spacing: 0.5px; line-height: 34px; }
  .main-nav { position: absolute; right: 33px; top: 15px; display: flex; gap: 13px; font-family: "Catamaran", sans-serif; font-size: 13.4px; color: var(--white); line-height: 18px; }
  .main-nav .active { color: var(--yellow); }

  .hero { position: absolute; left: 0; top: 47px; width: 928px; height: 465px;
    background: linear-gradient(180deg, #dfe8d8 0%, #c9cfc4 30%, #a9a49b 60%, #8b847b 100%); }
  .hero-band { position: absolute; left: 0; top: 358px; width: 928px; height: 154px; background: var(--band); }
  .hero-points { position: absolute; left: 33px; top: 382px; list-style: none; font-family: "Raleway", sans-serif; font-size: 13px; color: var(--white); }
  .hero-points li { display: flex; align-items: center; gap: 5px; height: 23.2px; }
  .hero-points .dot { width: 10px; height: 10px; border-radius: 50%; background: var(--yellow); flex: none; }
  .cta { position: absolute; left: 718px; top: 427px; width: 178px; height: 41px; background: var(--yellow);
    display: flex; align-items: center; justify-content: center; gap: 6px; font-family: "Raleway", sans-serif; font-size: 14.5px; color: #5b4a05; }

  .dropdown { position: absolute; left: 468px; top: 47px; width: 182px; height: 106px; background: var(--white);
    box-shadow: 0 1px 4px rgba(0,0,0,0.35); padding: 12px 10px 0 13px; }
  .dropdown::before { content: ""; position: absolute; left: 15px; top: -6px; border: 6px solid transparent; border-top: 0; border-bottom-color: var(--white); }
  .dropdown li { list-style: none; font-family: "Catamaran", sans-serif; font-size: 10px; color: var(--ink); height: 22px; line-height: 22px; border-bottom: 1px solid #e2e2e2; }
  .dropdown li:last-child { border-bottom: 0; }

  .col-rule { position: absolute; left: 458px; top: 555px; width: 1px; height: 415px; background: var(--rule); }
  .section-title { font-family: "Catamaran", sans-serif; font-weight: 500; font-size: 22px; color: var(--ink); letter-spacing: 0.3px; }

  .welcome { position: absolute; left: 34px; top: 572px; width: 410px; }
  .welcome .photo { position: absolute; left: 0; top: 51px; width: 103px; height: 141px; background: var(--photo-block); }
  .welcome .copy { position: absolute; left: 121px; top: 46px; width: 280px; font-size: 12.1px; line-height: 16.3px; }
  .welcome .copy p + p { margin-top: 16px; }

  .results { position: absolute; left: 490px; top: 572px; width: 397px; }
  .results ul { list-style: none; margin-top: 5px; }
  .results li { display: flex; gap: 6px; font-size: 12.1px; line-height: 16.3px; padding: 7px 0 8px; border-bottom: 1px solid var(--rule); }
  .results li:last-child { border-bottom: 0; }
  .results li svg { flex: none; margin-top: 3px; }
  .results li.highlight { color: var(--yellow); }
  .contact-note { margin-top: 6px; margin-left: -3px; font-family: "Catamaran", sans-serif; font-size: 17px; line-height: 20px; color: var(--ink); }
  .contact-note .accent { color: var(--green); }

  .memberships { position: absolute; left: 0; top: 1002px; width: 928px; height: 127px; background: var(--green); text-align: center; color: var(--white); }
  .memberships h2 { margin-top: 28px; font-family: "Catamaran", sans-serif; font-weight: 500; font-size: 21px; letter-spacing: 0.4px; }
  .memberships p { font-size: 11.8px; line-height: 16.3px; }
  .memberships span + span { margin-left: 10px; }

  .site-footer { position: absolute; left: 0; top: 1149px; width: 928px; text-align: center; }
  .site-footer .address { font-size: 10px; color: var(--muted); }
  .site-footer .terms { margin-top: 4px; font-size: 8px; color: var(--ink); }
</style>
</head>
<body>
  <header class="site-header">
    <div class="brand">TOVIMAR INC</div>
    <nav class="main-nav">
      <span>HOME</span><span>COMPANY</span><span>SERVICES</span>
      <span class="active">HOUSING REHAB APPLICATION</span>
      <span>AFFORDABLE APPLICATION</span><span>CONTACT</span>
    </nav>
  </header>

  <section class="hero" role="img" aria-label="Photo of a planning team in hard hats meeting around a clipboard"></section>
  <div class="hero-band"></div>
  <ul class="hero-points">
    <li><span class="dot"></span>Community Development Planning</li>
    <li><span class="dot"></span>Housing Rehabilitation Administration</li>
    <li><span class="dot"></span>US Department of Housing and Urban Development (HUD) Program Management</li>
    <li><span class="dot"></span>Implementation of Programs under the Jurisdiction of New Jersey Council of Affordable Housing (COAH)</li>
  </ul>
  <div class="cta">CALL TO ACTION
    <svg width="8" height="10" viewBox="0 0 8 10"><path d="M1.5 1 L6 5 L1.5 9" fill="none" stroke="#5b4a05" stroke-width="2"/></svg>
  </div>

  <ul class="dropdown">
    <li>LAKEWOOD</li><li>BRICK</li><li>JACKSON</li><li>WARREN</li>
  </ul>

  <div class="col-rule"></div>

  <section class="welcome">
    <h1 class="section-title">WELCOME TO TOVIMAR</h1>
    <div class="photo" role="img" aria-label="Photo of a surveyor with a laptop beside a tripod instrument in a field"></div>
    <div class="copy">
      <p>Tovimar, Inc. is a city planning firm that specializes in community development and housing rehabilitation program planning, design and implementation. We have over twenty years of experience in developing and administering income base-base housing and programs in accordance with US Department of Housing and Urban Development (HUD) and New Jersey Council on Affordable Housing (COAH) rules and regulations,</p>
      <p>In addition, our firm is capable of providing the technical and administrative assistance our clients require for implementation of their income based housing programs. Marlow Hendry Associates is one of the most experience urban planning firms in New Jersey, with over forty years of as consulting planners.</p>
      <p>To find out more about federal housing programs that we will administer, please go to www.federalhousinginfo.org</p>
    </div>
  </section>

  <section class="results">
    <h2 class="section-title">WE GET RESULTS</h2>
    <ul>
      <li><svg width="11" height="10" viewBox="0 0 11 10"><path d="M1 5 L4 8.5 L10 1" fill="none" stroke="#b5b5b5" stroke-width="2"/></svg><span>Tovimar designs income based programs to be supported by federal placement lotteries state funding.</span></li>
      <li><svg width="11" height="10" viewBox="0 0 11 10"><path d="M1 5 L4 8.5 L10 1" fill="none" stroke="#b5b5b5" stroke-width="2"/></svg><span>We implement local programs to benefit people seeking access to affordable housing.</span></li>
      <li><svg width="11" height="10" viewBox="0 0 11 10"><path d="M1 5 L4 8.5 L10 1" fill="none" stroke="#b5b5b5" stroke-width="2"/></svg><span>Our experienced staff screen applicants for local affordable housing.</span></li>
      <li><svg width="11" height="10" viewBox="0 0 11 10"><path d="M1 5 L4 8.5 L10 1" fill="none" stroke="#b5b5b5" stroke-width="2"/></svg><span>We pre-qualify persons who have applied for housing rehabilitation.</span></li>
      <li class="highlight"><svg width="11" height="10" viewBox="0 0 11 10"><path d="M1 5 L4 8.5 L10 1" fill="none" stroke="#f2c300" stroke-width="2.2"/></svg><span>Conduct placement lotteries</span></li>
      <li><svg width="11" height="10" viewBox="0 0 11 10"><path d="M1 5 L4 8.5 L10 1" fill="none" stroke="#b5b5b5" stroke-width="2"/></svg><span>Through local housing rehabilitation programs, our experience construction inspectors determine what improvements are required at eligible units based on local building codes and health and safety issues.</span></li>
    </ul>
    <p class="contact-note">For more information about out services,<br>please contact us today at <span class="accent">TOVIMAR (555) 214-3380<br>or tovimar@planmail.example</span></p>
  </section>

  <section class="memberships">
    <h2>MEMBERSHIPS</h2>
    <p><span>National Community Planning Alliance</span><span>Garden State Planning Association</span></p>
    <p>Garden State Planning Officials Garden State Community Development Network</p>
  </section>

  <footer class="site-footer">
    <p class="address">Copy Right 2014 Tovimar, 118 Harbor View Road, Brick, New Jersey, 08700 &nbsp; TEL (555) 214-3380 Fax (555) 214-3391</p>
    <p class="terms">©2014 - Terms</p>
  </footer>
</body>
</html>
```